Residential Remodeling Contractor needs updated business card

I need a new design for my business card.
Name of the company is Ridgefell Construction. I need a card that commands presence, strength, integrity. I have been in business for 28 years. I am a Residential Remodeling Contractor that covers all aspects of a residential remodel and build.

```html
<!DOCTYPE html>
<html lang="en">
<head>
<meta charset="UTF-8">
<title>Ridgefell Construction – Business Card</title>
<link href="https://fonts.googleapis.com/css2?family=Montserrat:wght@400;600&display=swap" rel="stylesheet">
<style>
  :root {
    --backdrop: #3b3532;
    --card-blue: #1f3e80;
    --ink-white: #ffffff;
    --ink-soft: #dfe5f2;
    --divider: rgba(255,255,255,0.45);
  }
  * { margin: 0; padding: 0; box-sizing: border-box; }
  html, body { width: 1200px; height: 786px; overflow: hidden; }
  body {
    background: var(--backdrop);
    font-family: "Montserrat", sans-serif;
    display: flex;
    align-items: center;
    justify-content: center;
    gap: 40px;
  }
  .card {
    width: 540px;
    height: 309px;
    background: var(--card-blue);
    color: var(--ink-white);
    position: relative;
    box-shadow: 0 10px 30px rgba(0,0,0,0.45);
  }
  .brand {
    display: flex;
    align-items: center;
    gap: 10px;
    font-weight: 600;
    text-transform: uppercase;
    letter-spacing: 1px;
    line-height: 1.1;
  }
  .brand-mark {
    width: 14px;
    height: 14px;
    background: var(--ink-white);
    flex: none;
  }
  .card-front .brand {
    position: absolute;
    left: 40px;
    top: 50%;
    transform: translateY(-50%);
    font-size: 17px;
  }
  .divider {
    position: absolute;
    left: 232px;
    top: 60px;
    bottom: 60px;
    width: 1px;
    background: var(--divider);
  }
  .contact {
    position: absolute;
    left: 256px;
    top: 64px;
    right: 20px;
    font-size: 11px;
    color: var(--ink-soft);
  }
  .contact-name {
    font-size: 17px;
    font-weight: 600;
    color: var(--ink-white);
  }
  .contact-role { margin-top: 2px; margin-bottom: 16px; font-size: 10px; }
  .contact-address { line-height: 1.35; margin-bottom: 14px; padding-left: 20px; }
  .contact-line {
    display: flex;
    align-items: center;
    gap: 10px;
    margin-bottom: 7px;
  }
  .contact-line svg { width: 12px; height: 12px; fill: var(--ink-white); flex: none; }
  .card-back {
    display: flex;
    align-items: center;
    justify-content: center;
  }
  .card-back .brand { font-size: 24px; }
  .card-back .brand-mark { width: 18px; height: 18px; }
</style>
</head>
<body>
  <section class="card card-front">
    <div class="brand">
      <span class="brand-mark"></span>
      <span>Ridgefell<br>Construction</span>
    </div>
    <div class="divider"></div>
    <div class="contact">
      <p class="contact-name">Daniel Harlow</p>
      <p class="contact-role">Owner</p>
      <p class="contact-address">48 Cedar Hollow Road<br>Brandon, MS 39042</p>
      <p class="contact-line">
        <svg viewBox="0 0 24 24" aria-hidden="true"><path d="M6.6 10.8a15 15 0 0 0 6.6 6.6l2.2-2.2a1 1 0 0 1 1-.25 11.4 11.4 0 0 0 3.6.57 1 1 0 0 1 1 1V20a1 1 0 0 1-1 1A17 17 0 0 1 3 4a1 1 0 0 1 1-1h3.5a1 1 0 0 1 1 1c0 1.25.2 2.45.57 3.57a1 1 0 0 1-.25 1z"/></svg>
        601.555.0147
      </p>
      <p class="contact-line">
        <svg viewBox="0 0 24 24" aria-hidden="true"><path d="M2 5h20v14H2z M2 5l10 7 10-7" /></svg>
        info@ridgefellconstruction.com
      </p>
      <p class="contact-line">
        <svg viewBox="0 0 24 24" aria-hidden="true"><path d="M12 2a10 10 0 1 0 0 20 10 10 0 0 0 0-20zm0 2c.9 1.2 1.7 2.9 2 5h-4c.3-2.1 1.1-3.8 2-5zM4.3 13a8 8 0 0 1 0-2h3.7a16 16 0 0 0 0 2zm.8 2h3.2c.3 1.6.8 3 1.5 4.1A8 8 0 0 1 5.1 15zm3.2-6H5.1a8 8 0 0 1 4.7-4.1C9.1 6 8.6 7.4 8.3 9zM12 20c-.9-1.2-1.7-2.9-2-5h4c-.3 2.1-1.1 3.8-2 5zm2.3-7H9.7a14 14 0 0 1 0-2h4.6a14 14 0 0 1 0 2zm-.1 6.1c.7-1.1 1.2-2.5 1.5-4.1h3.2a8 8 0 0 1-4.7 4.1zM16 13a16 16 0 0 0 0-2h3.7a8 8 0 0 1 0 2zm-.3-4c-.3-1.6-.8-3-1.5-4.1A8 8 0 0 1 18.9 9z"/></svg>
        www.ridgefellconstruction.com
      </p>
    </div>
  </section>

  <section class="card card-back">
    <div class="brand">
      <span class="brand-mark"></span>
      <span>Ridgefell<br>Construction</span>
    </div>
  </section>
</body>
</html>
```